Brochure Design Project

PLEASE USE THE ATTACHED WORD DOC ONLY AS A GUIDE- I WANT TO SEE A TRUE DESIGN AND NOT JUST A RECREATE OF MY CONTENT.

We need a brochure that is geared towards a service mentality. less tech/bold and something very approachable.

we will look for a design concept and then finalize the content laters.

Target Market(s)

nurses and business owners

Industry/Entity Type

Tech

```html
<!DOCTYPE html>
<html lang="en">
<head>
<meta charset="utf-8">
<title>Bayside Pharmacy – Customized Health Care Brochure</title>
<link rel="stylesheet" href="https://fonts.googleapis.com/css2?family=Bitter:ital,wght@1,500;1,600&family=Source+Sans+3:ital,wght@0,400;1,400&display=swap">
<style>
  :root {
    --coral: #ef4f5a;
    --blue: #1b8fcb;
    --blue-deep: #0f7fbf;
    --sky: #3cc0ec;
    --ink: #2f2f2f;
    --cream: #fdfbef;
    --butter: #fbf3b8;
    --page: #ffffff;
  }
  * { margin: 0; padding: 0; box-sizing: border-box; }
  html, body { width: 1200px; height: 928px; overflow: hidden; background: var(--page); }
  .brochure {
    position: relative; width: 1200px; height: 928px; overflow: hidden;
    font-family: "Source Sans 3", "Myriad Pro", sans-serif; color: var(--ink);
    background: var(--page);
  }
  .top-band {
    position: absolute; left: 0; top: 0; width: 1200px; height: 30px;
    background: linear-gradient(to bottom, var(--butter), #fdf8d8);
  }
  .corner-wash {
    position: absolute; left: 0; top: 30px; width: 520px; height: 260px;
    background: radial-gradient(ellipse at 40% 0%, rgba(27,143,203,0.08), rgba(27,143,203,0) 70%);
  }
  .bottom-band {
    position: absolute; left: 0; bottom: 0; width: 1200px; height: 32px;
    background: linear-gradient(to right, #0a86c4, var(--sky) 50%, #0a86c4);
  }
  .headline {
    position: absolute; left: 31px; top: 70px; width: 360px;
    font-family: "Bitter", Georgia, serif; font-style: italic; font-weight: 500;
    font-size: 50px; line-height: 57px; color: var(--coral);
  }
  .intro {
    position: absolute; left: 31px; top: 250px; width: 350px;
    font-size: 28px; line-height: 36px; color: #333;
  }
  .rule { position: absolute; top: 451px; height: 12px; }
  .rule--blue { left: 31px; width: 338px; background: linear-gradient(to right, #0c7fc0, var(--sky)); }
  .rule--coral { left: 831px; width: 338px; background: var(--coral); }
  .team-photo { position: absolute; left: 400px; top: 62px; width: 400px; height: 401px; }
  .services-box {
    position: absolute; left: 831px; top: 62px; width: 338px; height: 359px;
    background: var(--cream); box-shadow: 2px 3px 8px rgba(0,0,0,0.35);
    padding: 16px 14px 0 16px;
  }
  .services-box h2 {
    font-weight: 400; font-size: 31px; line-height: 36px; color: var(--blue);
    margin-bottom: 4px;
  }
  .services-box ul { list-style: none; }
  .services-box li {
    position: relative; padding-left: 10px; font-style: italic;
    font-size: 19px; line-height: 25px; color: #2a2a2a; margin-bottom: 7px;
  }
  .services-box li::before {
    content: "•"; position: absolute; left: 0; top: 0; color: var(--blue); font-style: normal; font-size: 14px;
  }
  .feature {
    position: absolute; width: 342px; font-size: 16.6px; line-height: 21.8px; color: #333;
  }
  .feature h3 {
    display: inline; font-family: "Bitter", Georgia, serif; font-style: italic; font-weight: 500;
    font-size: 20px; color: var(--blue); letter-spacing: -0.2px;
  }
  .col-1 { left: 31px; }
  .col-2 { left: 431px; }
  .col-3 { left: 831px; }
</style>
</head>
<body>
<main class="brochure">
  <div class="top-band"></div>
  <div class="corner-wash"></div>

  <h1 class="headline">Experts in Customized health care</h1>
  <p class="intro">By compounding medications, we can improve patient outcomes and simplify medication administration caregivers.</p>

  <svg class="team-photo" role="img" aria-label="Photo of three pharmacists in white coats reviewing a blue patient folder" viewBox="0 0 400 401" preserveAspectRatio="none">
    <defs>
      <linearGradient id="photoTone" x1="0" y1="0" x2="1" y2="1">
        <stop offset="0" stop-color="#eef3f8"/>
        <stop offset="0.55" stop-color="#d9e4ee"/>
        <stop offset="1" stop-color="#a9c2da"/>
      </linearGradient>
    </defs>
    <rect width="400" height="401" fill="url(#photoTone)"/>
  </svg>

  <aside class="services-box">
    <h2>We also provide:</h2>
    <ul>
      <li>Customized Combinations simplify medication admistration</li>
      <li>Dosage form Changes</li>
      <li>Transdermal Pain Management for site specific therapy</li>
      <li>Sugar-Free therapy for diabetic patients</li>
      <li>Lactose Capsules</li>
      <li>Customized dosage for kidney or liver failure patients</li>
    </ul>
  </aside>

  <div class="rule rule--blue"></div>
  <div class="rule rule--coral"></div>

  <section class="feature col-1" style="top:496px"><h3>Service:</h3> Our service sets us apart from retail pharmacies as well as large impersonal pharmacies. As your pharmacy partner, you’ll have access to our pharmacy owners knowledge staff to address concerns, find solutions, and ultimately provide better care while increasing your profitability.</section>
  <section class="feature col-1" style="top:672px"><h3>Timely Deliveries</h3> When it comes to timely deliveries, Bayside has multiple solutions to get you the medications you need quickly. With our pharmacy network, we can deliver medications at anytime, for any reason.</section>
  <section class="feature col-1" style="top:807px"><h3>MAR or EMAR</h3> We support EMAR or provide paper MARs if desired. Our goal is to work with your current system, not against it.</section>

  <section class="feature col-2" style="top:496px"><h3>Customized Formularies</h3> We help you manage healthcare costs and limit staff dispensing time by creating formularies that focus on generic and customized compounded medications.</section>
  <section class="feature col-2" style="top:627px"><h3>Technology Solutions</h3> Bayside provides great time saving technology solutions that you won’t find with other local retail pharmacies. We are constantly offer new and exciting ways to reduce staff time and increase profitability</section>
  <section class="feature col-2" style="top:785px"><h3>Medicare Part D Partners</h3> We handle therapeutic interchange, prior authorizations, and physician global authorizations so you don’t have to.</section>

  <section class="feature col-3" style="top:496px"><h3>Medicare Part A</h3> Utilizing our pharmacy network, we minimize billing issues with price transparency and accuracy. This allows us focus on corporate strategies to manage your pharmacy expenses. Monthly reports helps identify trends, non-formulary utilization and clinical standards to ensure your facility is saving time and money.</section>
  <section class="feature col-3" style="top:693px"><h3>Consultant Pharmacists</h3> Our pharmacists provide regulatory compliance assistance to minimize your risk and reduce issues during facility surveys.</section>
  <section class="feature col-3" style="top:822px"><h3>Continuing Education</h3> CE for caretakers leads to better outcomes for your residents and your bottom line.</section>

  <div class="bottom-band"></div>
</main>
</body>
</html>
```